Hong Kong based International Remittance and ForEx company requires website design

We need a website designed for a new European - Hong Kong based ForEx & fund remittence entity.

The company specialises in larger corporate & high net worth private client trades, therefore the design must aesthetically reflect this (sophisticated). As a theme colour, financial entities tend to use either blue or red; if blue, our preference is a darker blue. Visually, our preference is less copy, more imagery.

Number of pages would be limited; landing (home), about us, client registration (x1 Corporate form, x1 Private Client form), Contact Us.

Have uploaded the existing logo - please note this is to be redesigned, although the colour scheme will remain the same. Please also note that copy will follow - please use Lorem Ipsum.

Target Market(s)

Medium to large Corporations. High net worth individuals.

Industry/Entity Type

Financial Service

Coding

Coded - Design and coding required

Number of Pages Required

4 page

Font styles to use
Serif

Requirements
Nice to have
• ForEx ticker,

```html
<!DOCTYPE html>
<html lang="en">
<head>
<meta charset="utf-8">
<title>Harbourline Incorporation</title>
<link href="https://fonts.googleapis.com/css2?family=Lora:ital,wght@0,400;0,700;1,400&family=Open+Sans:ital,wght@0,400;0,600;0,700;1,400;1,600&display=swap" rel="stylesheet">
<style>
:root{
  --red:#d0202a;
  --red-dark:#b3161f;
  --navy:#0d4a8c;
  --ink:#222;
  --grey:#666;
  --light:#f4f4f4;
  --footer:#1c2430;
  --footer-line:#2c3543;
  --up:#6fc23a;
  --down:#e2262c;
}
*{box-sizing:border-box;margin:0;padding:0}
html,body{width:796px;height:1200px;overflow:hidden;background:#fff}
body{position:relative;font-family:"Open Sans",sans-serif;color:var(--ink)}
.abs{position:absolute}

/* header */
.site-header{left:0;top:0;width:796px;height:64px;background:#fff;border-top:2px solid var(--red);z-index:3}
.brand{left:58px;top:8px;width:124px;text-align:center}
.brand-mark{width:40px;height:40px;border-radius:50%;background:var(--red);margin:0 auto 3px}
.brand-name{font-family:"Lora",serif;font-weight:700;font-size:10px;letter-spacing:1px;color:var(--ink)}
.nav{left:205px;top:24px;display:flex;gap:18px;font-family:"Lora",serif;font-size:10.5px;color:#333;align-items:center}
.nav .active{color:var(--red)}
.lang{left:646px;top:22px;display:flex;align-items:center;gap:6px;font-size:8.5px;color:#777;letter-spacing:.5px}

/* hero */
.hero{left:0;top:64px;width:796px;height:284px;background:linear-gradient(100deg,#1b2029 0%,#243040 40%,#3a5c7c 65%,#4f7fa6 80%,#2b4763 100%)}
.hero h1{left:63px;top:84px;font-family:"Lora",serif;font-weight:700;font-size:36px;color:#fff}
.hero p{left:65px;top:134px;width:390px;font-style:italic;font-weight:600;font-size:11.5px;line-height:19px;color:#fff}
.btn-outline{left:65px;top:185px;width:99px;height:31px;border:2px solid #fff;background:var(--red);color:#fff;font-size:9.5px;font-weight:700;display:flex;align-items:center;justify-content:center;border-radius:2px}
.dots{left:372px;top:244px;display:flex;gap:2px}
.dots span{width:12px;height:12px;border:1.5px solid #fff;border-radius:50%}

/* ticker */
.ticker{left:0;top:348px;width:796px;height:30px;background:#0f1216;color:#fff;font-size:10.5px}
.ticker .track{left:51px;top:8px;white-space:nowrap}
.up{color:var(--up)}.down{color:var(--down)}
.ticker .arrow{top:0;width:34px;height:30px;display:flex;align-items:center;justify-content:center}

/* welcome */
.section-title{font-family:"Lora",serif;font-weight:700;font-size:15px;color:#222}
.welcome-img{left:65px;top:443px;width:175px;height:138px;border:2px solid #fff;box-shadow:0 0 0 1px #ddd;background:linear-gradient(135deg,#1a3a6a,#2a5a96 55%,#0e2344)}
.welcome-text{left:258px;top:438px;width:192px;font-size:8px;line-height:14.7px;color:#555}
.btn{background:var(--red);color:#fff;font-size:8px;font-weight:700;display:flex;align-items:center;justify-content:center;border-radius:2px}
.converter{left:471px;top:430px;width:258px;height:151px;background:var(--navy);border:2px solid #fff;box-shadow:0 0 0 1px #ccc;overflow:hidden}
.hang{top:378px;width:2px;height:62px;background:#e8dde4}
.peg{width:13px;height:13px;border-radius:50%;background:#fff;border:2px solid #e8dde4}
.field{background:#fff;height:25px;font-size:8.5px;color:#555;display:flex;align-items:center;padding-left:7px}
.select-arrow{right:0;top:0;width:28px;height:25px;background:#c9c9c9;display:flex;align-items:center;justify-content:center}
.result{color:#fff;font-size:8.5px}
.result b{font-size:11px}

/* expertise */
.expertise{left:0;top:617px;width:796px;height:244px;background:linear-gradient(90deg,#1d4d86 0%,#2a4c80 40%,#3d3f73 70%,#5a3a5e 100%)}
.expertise h2{left:0;top:22px;width:796px;text-align:center;font-family:"Lora",serif;font-size:15px;font-weight:700;color:#fff}
.service{top:68px;width:220px;text-align:center;color:#fff}
.service .ring{width:74px;height:74px;margin:0 auto;border-radius:50%;background:var(--red);border:3px solid #fff;display:flex;align-items:center;justify-content:center}
.service h3{font-family:"Lora",serif;font-size:11px;font-weight:700;margin-top:16px}
.service p{width:190px;margin:8px auto 0;font-size:8px;line-height:14.5px;color:#e2e6ee}

/* testimonial */
.quote-bg{left:92px;top:890px;width:73px;height:73px;border-radius:50%;background:#e3e3e3;color:#c6c6c6;font-family:"Lora",serif;font-weight:700;font-size:52px;line-height:80px;padding-left:10px}
.portrait{left:139px;top:890px;width:74px;height:74px;border-radius:50%;background:linear-gradient(160deg,#c8ccd2,#5a6270 60%,#2a3140)}
.testimonial{left:232px;top:892px;width:466px;font-style:italic;font-size:8.3px;line-height:18.3px;color:#555}
.author{left:232px;top:955px;font-family:"Lora",serif;font-size:10px;font-weight:700;color:var(--red)}
.chev{top:917px;color:#aaa;font-size:18px}

/* footer */
.footer{left:0;top:998px;width:796px;height:202px;background:var(--footer);color:#fff}
.footer h4{font-family:"Lora",serif;font-size:11.5px;font-weight:700}
.footer-col{top:22px;font-size:8px;line-height:17px;color:#e5e7ea}
.fbrand{left:65px;top:24px;width:140px;text-align:center}
.fbrand .brand-mark{width:66px;height:66px;background:#fff;margin-bottom:10px}
.fbrand .brand-name{color:#fff;font-size:16px;letter-spacing:1.5px}
.input{width:174px;height:22px;background:#fff;color:#777;font-size:8px;display:flex;align-items:center;padding-left:10px;margin-top:10px}
.subscribe{width:66px;height:24px;border:1.5px solid #fff;background:var(--red);font-size:8px;font-weight:700;display:flex;align-items:center;justify-content:center;margin-top:8px;border-radius:2px}
.contact-row{display:flex;gap:10px;align-items:flex-start;margin-bottom:6px;line-height:10px}
.contact-row svg{flex:none;margin-top:1px}
.footer-divider{left:65px;top:152px;width:666px;height:1px;background:var(--footer-line)}
.copyright{left:66px;top:173px;font-size:8px;color:#e5e7ea}
.social{top:164px;width:24px;height:24px;border:1.5px solid #fff;border-radius:50%}
.vdiv{top:22px;width:1px;height:120px;background:var(--footer-line)}
</style>
</head>
<body>

<header class="site-header abs">
  <div class="brand abs"><div class="brand-mark"></div><div class="brand-name">HARBOURLINE</div></div>
  <nav class="nav abs">
    <span class="active">Home</span><span>About Us</span><span>International Payments</span><span>Client Application</span><span>Contact Us</span>
    <svg width="10" height="10" viewBox="0 0 10 10"><circle cx="4" cy="4" r="3" fill="none" stroke="#333" stroke-width="1.5"/><line x1="6.3" y1="6.3" x2="9" y2="9" stroke="#333" stroke-width="1.6"/></svg>
  </nav>
  <div class="lang abs"><span style="width:30px;height:12px;background:var(--red);display:inline-block;border-radius:2px"></span>LANGUAGE</div>
</header>

<section class="hero abs" role="img" aria-label="Photograph of a hand reaching toward glowing financial figures and percentages on a dark blue screen">
  <h1 class="abs">Harbourline Incorporation</h1>
  <p class="abs">We are a new ForEx &amp; fund remittance entity based in European. We Excel in larger corporate &amp; high net worth private client trades.</p>
  <div class="btn-outline abs">GET MORE INFO</div>
  <div class="dots abs"><span></span><span></span><span></span><span></span></div>
</section>

<div class="ticker abs">
  <div class="arrow abs" style="left:0"><svg width="12" height="10" viewBox="0 0 12 10"><path d="M6 1 2 5l4 4M11 1 7 5l4 4" fill="none" stroke="#fff" stroke-width="1.6"/></svg></div>
  <div class="track abs">Alpha ALPH 380.11 <span class="up">▲ 1.51 ▲ 0.50%</span> Alpha ALPH 380.11 <span class="down">▼ 1.51 ▼ 0.50%</span> INTL Busines NORD alph 380.11 <span class="up">▲ 1.51 ▲ 0.50%</span> Alpha ALPH 380.11</div>
  <div class="arrow abs" style="left:762px;background:#0f1216"><svg width="12" height="10" viewBox="0 0 12 10"><path d="M1 1l4 4-4 4M6 1l4 4-4 4" fill="none" stroke="#fff" stroke-width="1.6"/></svg></div>
</div>

<h2 class="section-title abs" style="left:65px;top:404px">Welcome to Harbourline</h2>
<div class="welcome-img abs" role="img" aria-label="Photograph of a currency exchange rate board"></div>
<div class="welcome-text abs">Harbourline Incorporation Limited is a regulated Money Service Operator Number (18-04-02265), licensed authorised by the Hong Kong Customs and Excise.<br><br>We provide the international settlement and reconciliation of funds ..</div>
<div class="btn abs" style="left:258px;top:553px;width:81px;height:29px">READ MORE &gt;&gt;</div>

<div class="hang abs" style="left:517px"></div>
<div class="hang abs" style="left:681px"></div>
<div class="converter abs">
  <div class="field abs" style="left:11px;top:30px;width:70px">100</div>
  <div class="field abs" style="left:89px;top:30px;width:154px">British Pound Sterling<div class="select-arrow abs"><svg width="8" height="5"><path d="M0 0h8L4 5z" fill="#555"/></svg></div></div>
  <div class="field abs" style="left:11px;top:64px;width:70px">1078.05</div>
  <div class="field abs" style="left:89px;top:64px;width:154px">Hong Kong Dollar<div class="select-arrow abs"><svg width="8" height="5"><path d="M0 0h8L4 5z" fill="#555"/></svg></div></div>
  <div class="result abs" style="left:12px;top:102px"><b>100.00</b></div>
  <div class="result abs" style="left:80px;top:104px">British Pound Sterling is</div>
  <div class="result abs" style="left:12px;top:121px"><b>1,078.040</b></div>
  <div class="result abs" style="left:80px;top:123px">Hong Kong Dollar</div>
</div>
<div class="peg abs" style="left:512px;top:437px"></div>
<div class="peg abs" style="left:676px;top:437px"></div>

<section class="expertise abs" role="img" aria-label="Background photograph of financial charts in blue and violet tones">
  <h2 class="abs">Our Expertise</h2>
  <div class="service abs" style="left:59px">
    <div class="ring"><svg width="32" height="22" viewBox="0 0 32 22"><rect x="1" y="1" width="30" height="20" rx="1" fill="none" stroke="#fff" stroke-width="2.5"/><circle cx="16" cy="11" r="5.5" fill="#fff"/><text x="16" y="14.5" font-size="9" text-anchor="middle" fill="#d0202a" font-family="Open Sans" font-weight="700">1</text></svg></div>
    <h3>International Money Transfer</h3>
    <p>Lorem ipsum dolor sit amet, consectetur adi pisi ng elit, sed do eiusmod tempor iunt ut labore et dolore magna aliqsmod</p>
  </div>
  <div class="service abs" style="left:292px">
    <div class="ring"><svg width="26" height="20" viewBox="0 0 26 20"><path d="M2 6h19M16 1l5 5-5 5M24 14H5M10 9l-5 5 5 5" fill="none" stroke="#fff" stroke-width="2.6"/></svg></div>
    <h3>Foreign Exchange</h3>
    <p>Lorem ipsum dolor sit amet, consectetur adi pisi ng elit, sed do eiusmod tempor iunt ut labore et dolore magna aliqsmod</p>
  </div>
  <div class="service abs" style="left:527px">
    <div class="ring"><svg width="28" height="26" viewBox="0 0 28 26"><rect x="1" y="1" width="26" height="17" rx="1.5" fill="#fff"/><rect x="11" y="18" width="6" height="4" fill="#fff"/><rect x="7" y="22" width="14" height="3" fill="#fff"/></svg></div>
    <h3>Paying &amp; Receiving Agency</h3>
    <p>Lorem ipsum dolor sit amet, consectetur adi pisi ng elit, sed do eiusmod tempor iunt ut labore et dolore magna aliqsmod</p>
  </div>
</section>

<div class="chev abs" style="left:64px">‹</div>
<div class="quote-bg abs">“</div>
<div class="portrait abs" role="img" aria-label="Portrait photograph of the client giving the testimonial"></div>
<p class="testimonial abs">It is a long established fact that a reader will be distracted by the readable content of a page when looking at its layout. The point of using Lorem Ipsum is that it has a more-or-less normal distribution of letters, as opposed to using 'Content here, content here', making it look like readable English.</p>
<div class="author abs">- Marcus Hale</div>
<div class="chev abs" style="left:720px">›</div>

<footer class="footer abs">
  <div class="fbrand abs"><div class="brand-mark"></div><div class="brand-name">HARBOURLINE</div></div>
  <div class="vdiv abs" style="left:231px"></div>
  <div class="footer-col abs" style="left:254px">
    <h4>Information</h4>
    <div style="margin-top:8px">Home<br>About us<br>International Payments<br>Client Applications<br>Contact Us</div>
  </div>
  <div class="vdiv abs" style="left:356px"></div>
  <div class="footer-col abs" style="left:378px;width:180px">
    <h4>Newsletter</h4>
    <div style="margin-top:8px;line-height:13.5px">Register Your email address to get information abiout us</div>
    <div class="input">Email Address</div>
    <div class="subscribe">SUBSCRIBE</div>
  </div>
  <div class="vdiv abs" style="left:566px"></div>
  <div class="footer-col abs" style="left:588px;width:160px">
    <h4>Contact Us</h4>
    <div style="margin-top:12px">
      <div class="contact-row"><svg width="7" height="10" viewBox="0 0 7 10"><path d="M3.5 0A3.5 3.5 0 0 0 0 3.5C0 6 3.5 10 3.5 10S7 6 7 3.5A3.5 3.5 0 0 0 3.5 0z" fill="#fff"/><circle cx="3.5" cy="3.5" r="1.3" fill="#1c2430"/></svg><span>27 Quayside Lane, Suite 4,<br>Harbour Point 5120</span></div>
      <div class="contact-row" style="margin-top:8px"><svg width="9" height="9" viewBox="0 0 9 9"><path d="M2 0l2 2-1 1.5a6 6 0 0 0 2.5 2.5L7 5l2 2-1.5 2C3.5 9 0 5.5 0 1.5z" fill="#fff"/></svg><span>(852) 2100 4417</span></div>
      <div class="contact-row" style="margin-top:8px"><svg width="10" height="9" viewBox="0 0 10 9"><rect x="0" y="3" width="10" height="6" fill="#fff"/><rect x="2" y="0" width="6" height="3" fill="#fff"/></svg><span>(852) 2100 4418</span></div>
      <div class="contact-row" style="margin-top:8px"><svg width="10" height="8" viewBox="0 0 10 8"><rect width="10" height="8" fill="#fff"/><path d="M0 0l5 4 5-4" fill="none" stroke="#1c2430"/></svg><span>info@harbourlineinc.com</span></div>
    </div>
  </div>
  <div class="footer-divider abs"></div>
  <div class="copyright abs">Copyrights ©2016, Harbourline Incorpation. All rights reserved.</div>
  <div class="social abs" style="left:621px"></div>
  <div class="social abs" style="left:649px"></div>
  <div class="social abs" style="left:677px"></div>
  <div class="social abs" style="left:706px"></div>
</footer>

</body>
</html>
```